Business Card Design Project

We are an incubator company that helps young entrepreneur to launch new ideas into the market. We will be targeting investors or likewise; Angels, young entrepreneurs and technopreneurs.

Our logo is being tasked by pixelhive to design, therefore there is no logo for now.
You can us Lanternfield Pte Ltd as the logo for the time being.

Please let us have some versions of modern and yet professional designs; for words, you can indicate e.g (address), (Title)

thanks

Target Market(s)

young entrepreneurs
angels, investors

Industry/Entity Type

Business

Colors
3176b5
ffffff

Requirements
Must have
• able to project out our name; Lanternfield
Should not have
• Nothing childish or cartoon

```html
<!DOCTYPE html>
<html lang="en">
<head>
<meta charset="utf-8">
<title>Lanternfield Pte Ltd — Business Card</title>
<link href="https://fonts.googleapis.com/css2?family=Quicksand:wght@400&family=Open+Sans:wght@400&display=swap" rel="stylesheet">
<style>
  :root {
    --backdrop: #7c7a76;
    --card-white: #ffffff;
    --teal: #03a0b7;
    --slate: #475867;
    --slate-deep: #3f4f5d;
    --contact-text: #93a8ba;
    --name-text: #ffffff;
  }
  * { margin: 0; padding: 0; box-sizing: border-box; }
  html, body {
    width: 1200px;
    height: 900px;
    overflow: hidden;
    background: var(--backdrop);
  }
  .canvas {
    position: relative;
    width: 1200px;
    height: 900px;
  }
  .business-card {
    position: absolute;
    left: 100px;
    top: 164px;
    width: 1000px;
    height: 572px;
    background: var(--card-white);
    overflow: hidden;
    box-shadow: 0 10px 30px rgba(0, 0, 0, 0.25);
  }
  .card-shapes {
    position: absolute;
    inset: 0;
    width: 100%;
    height: 100%;
  }
  .brand {
    position: absolute;
    left: 223px;
    top: 40px;
    display: flex;
    align-items: center;
    gap: 12px;
  }
  .brand-dot {
    width: 44px;
    height: 44px;
    border-radius: 50%;
    background: var(--slate);
  }
  .brand-name {
    font-family: "Quicksand", sans-serif;
    font-weight: 400;
    font-size: 31px;
    color: var(--slate);
    letter-spacing: 0.5px;
  }
  .person {
    position: absolute;
    left: 490px;
    top: 228px;
    width: 300px;
    text-align: right;
  }
  .person-name {
    font-family: "Open Sans", sans-serif;
    font-size: 34px;
    line-height: 1;
    color: var(--name-text);
  }
  .person-title {
    font-family: "Open Sans", sans-serif;
    font-size: 13px;
    color: var(--teal);
    margin-top: 1px;
    padding-right: 2px;
  }
  .contact-box {
    position: absolute;
    left: 505px;
    top: 330px;
    width: 305px;
    height: 72px;
    background: var(--slate-deep);
    display: flex;
    flex-direction: column;
    justify-content: center;
    align-items: center;
    font-family: "Open Sans", sans-serif;
    font-size: 19px;
    line-height: 1.3;
    color: var(--contact-text);
  }
</style>
</head>
<body>
<main class="canvas">
  <section class="business-card">
    <svg class="card-shapes" viewBox="0 0 1000 572" aria-hidden="true">
      <rect class="side-panel" x="28" y="36" width="180" height="410" fill="var(--teal)"/>
      <ellipse class="teal-wave" cx="790" cy="560" rx="420" ry="455" fill="var(--teal)"/>
      <ellipse class="slate-dome" cx="690" cy="600" rx="420" ry="435" fill="var(--slate)"/>
      <path class="slate-hill" d="M0 492 C 110 430, 250 430, 340 480 L 360 572 L 0 572 Z" fill="var(--slate)"/>
      <rect class="slate-base" x="0" y="540" width="1000" height="32" fill="var(--slate)"/>
    </svg>

    <header class="brand">
      <span class="brand-dot"></span>
      <span class="brand-name">Lanternfield Pte Ltd.</span>
    </header>

    <div class="person">
      <p class="person-name">Your name</p>
      <p class="person-title">designation</p>
    </div>

    <address class="contact-box">
      <span class="contact-email">contact@lanternfield.com</span>
      <span class="contact-web">lanternfield.com</span>
    </address>
  </section>
</main>
</body>
</html>
```